Design a WordPress layout for a home loans company

The home loans company in question is going through a rebrand and needs a new website layout.
Sites they like: http://www.brightkeylending.com.au/
Current logo: Attached.
Colours to be used: As per those used in logo.
Primary: #71aa3d
Secondary: #130e10
Pages to be designed:
- Homepage
- Internal services page
Menu items for display purposes:
- Home
- About Us
- Speak to a Broker
- Articles
- Contact Us
A modern design with simplicity is key.
For copy, dummy text such as Lorem ipsum will be fine.
If you would like anything elso, please ask.
Target Market(s)
25-40 year old
Mostly female
Buying their first home in most cases
Industry/Entity Type
Mortgage Brokerage
Number of Pages Required
2 page

```html
<!DOCTYPE html>
<html lang="en">
<head>
<meta charset="utf-8">
<title>Nestwell Home Loans</title>
<link href="https://fonts.googleapis.com/css2?family=Poppins:wght@400;500;600;700&family=Open+Sans:wght@400;600;700&display=swap" rel="stylesheet">
<style>
:root{
  --green:#71aa3d;
  --green-dark:#5e9330;
  --ink:#130e10;
  --text:#555;
  --muted:#999;
  --line:#e3e3e3;
  --white:#fff;
}
*{box-sizing:border-box;margin:0;padding:0}
html,body{width:1200px;height:3448px;overflow:hidden}
body{font-family:"Open Sans",Arial,sans-serif;color:var(--text);background:var(--white);position:relative}
h1,h2,h3,h4{font-family:"Poppins",Arial,sans-serif}
.green{color:var(--green)}
.btn{display:inline-block;font-family:"Poppins",Arial,sans-serif;font-weight:600;font-size:15px;padding:12px 28px;border-radius:24px;border:none}
.btn-green{background:var(--green);color:var(--white)}
.btn-dark{background:var(--ink);color:var(--white)}
.btn-white{background:var(--white);color:var(--green)}
.field{border:1px solid var(--line);border-radius:22px;height:44px;padding:0 18px;font-size:13px;color:var(--muted);display:flex;align-items:center;background:var(--white)}

/* header */
.topbar{position:absolute;top:0;left:0;width:1200px;height:92px}
.search{position:absolute;left:80px;top:28px;width:210px;height:36px;border:1px solid var(--line);display:flex;align-items:center;justify-content:space-between;padding:0 12px;font-size:13px;color:var(--muted)}
.brand{position:absolute;left:50%;top:18px;transform:translateX(-50%);display:flex;align-items:center;gap:10px;white-space:nowrap}
.brand-mark{width:22px;height:22px;background:var(--green)}
.brand-name{font-family:"Poppins",sans-serif;font-weight:600;font-size:26px;color:var(--green);line-height:1}
.phone{position:absolute;right:80px;top:34px;display:flex;align-items:center;gap:10px;font-size:15px;color:var(--ink)}
.nav{position:absolute;top:92px;left:0;width:1200px;height:56px;border-top:1px solid var(--line);border-bottom:1px solid var(--line)}
.nav ul{list-style:none;display:flex;justify-content:center;height:100%}
.nav li{width:136px;display:flex;align-items:center;justify-content:center;font-family:"Poppins",sans-serif;font-size:15px;color:var(--ink);white-space:nowrap}
.nav li.active{background:var(--green);color:var(--white)}

/* hero */
.hero{position:absolute;top:148px;left:0;width:1200px;height:564px;background:var(--green)}
.hero-photo{position:absolute;left:0;top:0;width:1200px;height:564px}
.hero-text{position:absolute;left:712px;top:190px;width:400px;color:var(--white)}
.hero-text h1{font-size:34px;font-weight:600;line-height:1.3;margin-bottom:18px}
.hero-text p{font-size:13px;line-height:1.7;margin-bottom:24px}

/* welcome */
.welcome{position:absolute;top:712px;left:0;width:1200px;height:428px;text-align:center;padding-top:76px}
.welcome h2{font-size:38px;font-weight:600;color:var(--ink);margin-bottom:30px}
.welcome p{width:700px;margin:0 auto 18px;font-size:14px;line-height:1.8}
.welcome .btn{margin-top:18px}

/* advice */
.advice{position:absolute;top:1140px;left:0;width:1200px;height:520px;background:var(--green);color:var(--white);text-align:center;padding-top:72px}
.advice h2{font-size:38px;font-weight:500;margin-bottom:22px}
.advice h2 b{font-weight:700;color:var(--ink)}
.advice p.lead{width:760px;margin:0 auto 26px;font-size:14px;line-height:1.8}
.advice h4{font-size:18px;font-weight:600;margin-bottom:44px}
.features{display:flex;justify-content:center;gap:110px}
.feature{width:230px}
.feature svg{display:block;margin:0 auto 14px}
.feature h3{font-size:18px;font-weight:600;margin-bottom:10px}
.feature p{font-size:14px;line-height:1.7}

/* find broker */
.broker{position:absolute;top:1660px;left:0;width:1200px;height:440px}
.broker-form{position:absolute;left:80px;top:70px;width:420px}
.broker-form h2{font-size:36px;font-weight:600;color:var(--ink);margin-bottom:24px}
.broker-form label{display:block;font-size:14px;font-weight:600;color:var(--ink);margin-bottom:10px}
.broker-form .field{width:420px;margin-bottom:22px}
.broker-photo{position:absolute;left:600px;top:0;width:600px;height:440px}

/* newsletter */
.newsletter{position:absolute;top:2100px;left:0;width:1200px;height:300px;background:var(--green);color:var(--white)}
.news-art{position:absolute;left:0;top:50px;width:340px;height:200px;border-radius:0 100px 100px 0;background:linear-gradient(135deg,#e9cfb3,#c9503a)}
.news-body{position:absolute;left:380px;top:78px}
.news-body h2{font-size:36px;font-weight:600;margin-bottom:10px}
.news-body h2 span{color:var(--ink)}
.news-body p{font-size:14px;margin-bottom:18px}
.news-row{display:flex;gap:14px}
.news-row .field{width:290px;background:transparent;border:2px solid var(--white);color:var(--white)}

/* articles */
.articles{position:absolute;top:2400px;left:0;width:1200px;height:480px;text-align:center}
.articles h2{font-size:36px;font-weight:600;color:var(--green);margin-top:46px}
.cards{position:absolute;left:80px;top:108px;width:1040px;display:flex;justify-content:space-between}
.card{width:320px;height:360px;position:relative;border-radius:4px;overflow:hidden}
.card-photo .ph{position:absolute;inset:0}
.card-photo .cap{position:absolute;left:20px;right:20px;bottom:60px;color:var(--white);font-family:"Poppins",sans-serif;font-weight:600;font-size:19px;line-height:1.3}
.card-photo .av,.card-text .av{width:40px;height:40px;border-radius:50%;background:#7c8a73;border:3px solid var(--white)}
.card-photo .av{position:absolute;left:140px;bottom:10px}
.card-text{background:var(--white);box-shadow:0 4px 18px rgba(0,0,0,.12);padding:40px 32px 0}
.card-text p{font-size:14px;line-height:1.8;margin-bottom:22px}
.card-text .av{margin:0 auto 6px}
.card-text small{display:block;font-size:12px;margin-bottom:10px}
.card-text .btn{font-size:13px;padding:9px 22px}
.arrow{position:absolute;top:260px;width:36px;height:36px;border-radius:50%;background:var(--green)}
.arrow.left{left:22px}.arrow.right{right:22px}

/* contact */
.contact{position:absolute;top:2880px;left:0;width:1200px;height:440px}
.contact-band{position:absolute;left:0;top:200px;width:1200px;height:368px;background:var(--green)}
.map{position:absolute;left:130px;top:60px;width:400px;height:320px;background:linear-gradient(135deg,#ecebe6,#d9d7cf)}
.contact-card{position:absolute;left:520px;top:52px;width:500px;height:340px;background:var(--white);box-shadow:0 4px 18px rgba(0,0,0,.12);padding:28px 40px;text-align:center}
.contact-card h2{font-size:34px;font-weight:600;color:var(--green);margin-bottom:18px}
.contact-card h2 span{color:var(--ink)}
.row{display:flex;gap:20px;margin-bottom:16px}
.row .field{flex:1}
.msg{height:90px;border:1px solid var(--line);border-radius:14px;text-align:left;padding:12px 18px;font-size:13px;color:var(--muted);margin-bottom:18px}

/* footer */
.footer{position:absolute;top:3320px;left:0;width:1200px;height:128px;background:var(--green);text-align:center;color:var(--white)}
.social{display:flex;justify-content:center;gap:14px;margin-top:18px}
.social span{width:30px;height:30px;border-radius:50%;background:var(--white)}
.footer hr{border:none;border-top:1px solid rgba(255,255,255,.4);width:1040px;margin:22px auto 16px}
.footer p{font-size:13px}
</style>
</head>
<body>

<header class="topbar">
  <div class="search">Search Here...
    <svg width="14" height="14" viewBox="0 0 14 14"><circle cx="6" cy="6" r="4.5" fill="none" stroke="#71aa3d" stroke-width="1.8"/><line x1="9.5" y1="9.5" x2="13" y2="13" stroke="#71aa3d" stroke-width="1.8"/></svg>
  </div>
  <div class="brand"><span class="brand-mark"></span><span class="brand-name">Nestwell Home Loans</span></div>
  <div class="phone">
    <svg width="16" height="16" viewBox="0 0 24 24"><path d="M6.6 10.8a15 15 0 0 0 6.6 6.6l2.2-2.2a1 1 0 0 1 1-.25 11 11 0 0 0 3.6.6 1 1 0 0 1 1 1V20a1 1 0 0 1-1 1A17 17 0 0 1 3 4a1 1 0 0 1 1-1h3.5a1 1 0 0 1 1 1 11 11 0 0 0 .6 3.6 1 1 0 0 1-.25 1z" fill="#130e10"/></svg>
    555 014 2290
  </div>
</header>
<nav class="nav">
  <ul>
    <li class="active">Home</li><li>About Us</li><li>Speak to a Broker</li><li>Articles</li><li>Contact Us</li>
  </ul>
</nav>

<section class="hero">
  <svg class="hero-photo" viewBox="0 0 1200 564" role="img" aria-label="Photo of a young couple reviewing home loan papers with a broker">
    <defs><linearGradient id="hg" x1="0" y1="0" x2="1" y2="1"><stop offset="0" stop-color="#d9d2c6"/><stop offset="1" stop-color="#8f7a66"/></linearGradient></defs>
    <polygon points="0,0 690,0 630,564 0,564" fill="url(#hg)"/>
  </svg>
  <div class="hero-text">
    <h1>Lowest Intrest Rate on Home Loan</h1>
    <p>Lorem Ipsum is simply dummy text of the printing and typesetting industry. Lorem Ipsum has been the industry's standard dummy text ever since the 1500s.</p>
    <span class="btn btn-dark">Contact Us</span>
  </div>
</section>

<section class="welcome">
  <h2>Welcome To <span class="green">Nestwell Home Loans</span></h2>
  <p>Lorem Ipsum is simply dummy text of the printing and typesetting industry. Lorem Ipsum has been the industry's standard dummy text ever since the 1500s, when an unknown printer took a galley of type and scrambled it to make a type specimen book.</p>
  <p>It has survived not only five centuries, but also the leap into electronic typesetting, remaining essentially unchanged. It was popularised in the 1960s with the release.</p>
  <span class="btn btn-green">Know More</span>
</section>

<section class="advice">
  <h2>Better advice through <b>better listening</b></h2>
  <p class="lead">Lorem Ipsum is simply dummy text of the printing and typesetting industry. Lorem Ipsum has been the industry's standard dummy text ever since the 1500s, when an unknown printer took a galley of type and scrambled it to make a type specimen book.</p>
  <h4>With a Nestwell Home Loans broker, you'll have</h4>
  <div class="features">
    <div class="feature">
      <svg width="40" height="40" viewBox="0 0 40 40" fill="none" stroke="#130e10" stroke-width="2.2"><rect x="6" y="10" width="28" height="22" rx="2"/><line x1="6" y1="17" x2="34" y2="17"/><line x1="12" y1="24" x2="22" y2="24"/></svg>
      <h3>Local experts</h3>
      <p>Lorem Ipsum is simply dummy text of the printing and typesetting industry.</p>
    </div>
    <div class="feature">
      <svg width="40" height="40" viewBox="0 0 40 40" fill="none" stroke="#130e10" stroke-width="2.2"><circle cx="20" cy="16" r="9"/><polyline points="14,23 12,36 20,31 28,36 26,23"/></svg>
      <h3>Local experts</h3>
      <p>Lorem Ipsum is simply dummy text of the printing and typesetting industry.</p>
    </div>
    <div class="feature">
      <svg width="40" height="40" viewBox="0 0 40 40" fill="none" stroke="#130e10" stroke-width="2.2"><rect x="6" y="18" width="7" height="16"/><path d="M13 19l6-10c2-2 5-1 4 3l-1 5h9c2 0 3 2 2 4l-3 10c-1 2-2 3-4 3H13"/></svg>
      <h3>Local experts</h3>
      <p>Lorem Ipsum is simply dummy text of the printing and typesetting industry.</p>
    </div>
  </div>
</section>

<section class="broker">
  <div class="broker-form">
    <h2><span class="green">Find a</span> Local Broker</h2>
    <label>Suburb/town</label>
    <div class="field">Enter a location</div>
    <label>or postcode</label>
    <div class="field"></div>
    <span class="btn btn-green">Find Broker</span>
  </div>
  <svg class="broker-photo" viewBox="0 0 600 440" role="img" aria-label="Photo of a happy family relaxing on a sofa at home">
    <defs><linearGradient id="bg2" x1="0" y1="0" x2="1" y2="1"><stop offset="0" stop-color="#f1f1ef"/><stop offset="1" stop-color="#c9c3b8"/></linearGradient></defs>
    <rect width="600" height="440" fill="url(#bg2)"/>
  </svg>
</section>

<section class="newsletter">
  <div class="news-art" role="img" aria-label="Illustration of a hand holding a small house"></div>
  <div class="news-body">
    <h2>News<span>letter</span></h2>
    <p>For latest news or updates please subscribe our newsletter</p>
    <div class="news-row">
      <div class="field">Enter name*</div>
      <div class="field">Enter e-mail*</div>
      <span class="btn btn-white">Subscribe</span>
    </div>
  </div>
</section>

<section class="articles">
  <h2>Articles</h2>
  <span class="arrow left"><svg width="36" height="36" viewBox="0 0 36 36"><polyline points="20,12 14,18 20,24" fill="none" stroke="#fff" stroke-width="2.5"/></svg></span>
  <span class="arrow right"><svg width="36" height="36" viewBox="0 0 36 36"><polyline points="16,12 22,18 16,24" fill="none" stroke="#fff" stroke-width="2.5"/></svg></span>
  <div class="cards">
    <div class="card card-photo">
      <svg class="ph" viewBox="0 0 320 360" role="img" aria-label="Photo of a broker meeting with clients"><rect width="320" height="360" fill="#8d7b6c"/></svg>
      <div class="cap">Lorem Ipsum is simply dummy text of the printing</div>
      <span class="av"></span>
    </div>
    <div class="card card-text">
      <p>Lorem Ipsum is simply dummy text of the printing and typesetting industry. Lorem Ipsum has been the industry's standard dummy text ever since the 1500s, when an unknown printer took a galley.</p>
      <div class="av"></div>
      <small>Admin Name</small>
      <span class="btn btn-green">Read More</span>
    </div>
    <div class="card card-photo">
      <svg class="ph" viewBox="0 0 320 360" role="img" aria-label="Photo of a couple planning their first home"><rect width="320" height="360" fill="#9a8571"/></svg>
      <div class="cap">Lorem Ipsum is simply dummy text of the printing</div>
      <span class="av"></span>
    </div>
  </div>
</section>

<section class="contact">
  <div class="contact-band"></div>
  <div class="map" role="img" aria-label="Street map showing the office location"></div>
  <div class="contact-card">
    <h2>Contact <span>Us</span></h2>
    <div class="row"><div class="field">Name</div><div class="field">E-mail</div></div>
    <div class="msg">Message</div>
    <span class="btn btn-green">Send Now</span>
  </div>
</section>

<footer class="footer">
  <div class="social"><span></span><span></span><span></span><span></span></div>
  <hr>
  <p>© NESTWELL HOME LOANS - 2018. All Rights Reserved.</p>
</footer>

</body>
</html>
```